Business card for a Exhibition booth fabrication company

Hi. My company would like to change our corporate name card. We are an events and Exhibition stand builder company. We would like our corporate name card to resonate what we do. I need someone to create something unique that relates to the industry that I am in. The graphic designer should be creative to incorporate the elements of my industry and try to blend in well in the design of the card. Our aim is to ensure that we are unique and our card can look different from our competitors.
Updates

Target Market(s)

Marketing and events manager from all companies

Contact Information for Business Card

The business card should have the following details:
Name
Job Title
Email
Website

Colors

Designer to choose colors to be used in the design.

Requirements
Must have
• The card must be look something that is relevant to the service that I am providing. My website is: www.velmora-buildworks.com
• You can see my website to get more information on what service that I am doing
Nice to have
• On the back of my card, I would like to have a globe image with the incorporation of my company logo. This is to indicate that my services can be done in any part of the world.

```html
<!DOCTYPE html>
<html lang="en">
<head>
<meta charset="utf-8">
<title>Velmora Buildworks – Business Card</title>
<link rel="stylesheet" href="https://fonts.googleapis.com/css2?family=Oswald:wght@700&family=Merriweather:wght@400&family=Open+Sans:wght@400&family=Montserrat:wght@600&display=swap">
<style>
  :root {
    --page: #e9e7e4;
    --card: #ffffff;
    --ink: #3b3b3d;
    --red: #e21d26;
    --maroon: #7c0d12;
    --charcoal: #404042;
    --map-light: #eeeeee;
    --map-dark: #c9c9c9;
  }
  html, body {
    margin: 0;
    width: 1200px;
    height: 1200px;
    overflow: hidden;
    background: var(--page);
  }
  .sheet {
    width: 1200px;
    height: 1200px;
    display: flex;
    flex-direction: column;
    align-items: center;
    justify-content: center;
    gap: 60px;
  }
  .card {
    position: relative;
    width: 840px;
    height: 480px;
    background: var(--card);
    box-shadow: 0 6px 18px rgba(0,0,0,0.18);
    overflow: hidden;
  }
  .card-back .world-map {
    position: absolute;
    left: 150px;
    top: 50px;
    width: 560px;
    height: 330px;
    border-radius: 50% 50% 40% 40% / 60% 60% 40% 40%;
    background: radial-gradient(ellipse at center, var(--map-dark) 0%, var(--map-light) 70%, rgba(255,255,255,0) 100%);
    opacity: 0.8;
  }
  .brand {
    position: absolute;
    display: flex;
    align-items: center;
    gap: 14px;
    font-family: "Montserrat", sans-serif;
    font-weight: 600;
    letter-spacing: 4px;
    color: var(--ink);
    white-space: nowrap;
  }
  .brand-mark {
    width: 22px;
    height: 22px;
    background: var(--red);
    flex: none;
  }
  .card-back .brand {
    left: 0; right: 0;
    top: 250px;
    justify-content: center;
    font-size: 34px;
  }
  .card-back .brand .brand-mark { width: 30px; height: 30px; }

  .card-front .brand {
    right: 44px;
    top: 128px;
    font-size: 21px;
    letter-spacing: 3px;
    gap: 12px;
  }
  .card-front .brand .brand-mark { width: 20px; height: 20px; }
  .holder-name {
    position: absolute;
    left: 40px;
    top: 118px;
    margin: 0;
    font-family: "Oswald", sans-serif;
    font-weight: 700;
    font-size: 50px;
    line-height: 1;
    color: var(--charcoal);
  }
  .holder-name .first { color: var(--red); }
  .holder-title {
    position: absolute;
    left: 42px;
    top: 174px;
    margin: 0;
    font-family: "Merriweather", serif;
    font-size: 17px;
    color: var(--ink);
  }
  .rule { position: absolute; top: 204px; height: 3px; }
  .rule-dark { left: 40px; width: 330px; background: var(--charcoal); }
  .rule-red { left: 370px; right: 0; height: 2px; top: 205px; background: var(--red); }
  .contacts {
    position: absolute;
    left: 40px;
    top: 220px;
    margin: 0;
    padding: 0;
    list-style: none;
    font-family: "Open Sans", sans-serif;
    font-size: 19px;
    color: var(--ink);
  }
  .contacts li { display: flex; align-items: center; gap: 12px; height: 30px; }
  .contacts svg { width: 20px; height: 20px; flex: none; }
  .band { position: absolute; top: 300px; height: 150px; }
  .band-charcoal { left: 0; width: 150px; background: var(--charcoal); }
  .band-maroon { left: 162px; width: 140px; background: var(--maroon); }
  .band-red { left: 314px; width: 450px; background: var(--red); }
</style>
</head>
<body>
<main class="sheet">
  <section class="card card-back">
    <div class="world-map" role="img" aria-label="Faint grey world map behind the company name"></div>
    <div class="brand"><span class="brand-mark"></span>VELMORA BUILDWORKS</div>
  </section>

  <section class="card card-front">
    <h1 class="holder-name"><span class="first">Daniel</span> Hart</h1>
    <p class="holder-title">Managing Director</p>
    <div class="rule rule-dark"></div>
    <div class="rule rule-red"></div>
    <ul class="contacts">
      <li>
        <svg viewBox="0 0 20 20" aria-hidden="true"><rect x="1" y="4" width="18" height="12" rx="2" fill="#e21d26"/><path d="M2 5 L10 11 L18 5" stroke="#fff" stroke-width="1.6" fill="none"/></svg>
        username@velmora-buildworks.com
      </li>
      <li>
        <svg viewBox="0 0 20 20" aria-hidden="true"><circle cx="10" cy="10" r="9" fill="#e21d26"/><g stroke="#fff" stroke-width="1.2" fill="none"><circle cx="10" cy="10" r="6"/><ellipse cx="10" cy="10" rx="2.6" ry="6"/><line x1="4" y1="10" x2="16" y2="10"/></g></svg>
        www.velmora-buildworks.com
      </li>
    </ul>
    <div class="brand"><span class="brand-mark"></span>VELMORA BUILDWORKS</div>
    <div class="band band-charcoal"></div>
    <div class="band band-maroon"></div>
    <div class="band band-red"></div>
  </section>
</main>
</body>
</html>
```